The Kestrel Personal Training Studio Information Card

The front and back of card to give people that walk in to our gym. There are a few things to say on the card. But it also needs to be designed in an attractive way. You can make some of the information bullett points or with icons or graphics. Please look at our website at https://thekestreltraining.com/ . The card will be 4" x 9"

Target Market(s)

High End Clientele who want to train in a private gym

Industry/Entity Type

Fitness

Font styles to use
Serif
Sans Serif
Other font styles liked:
• the same font Borvale uses on the veltab

Colors
F0912C
F2A743
F7CA91
FBE8D2
FDF5EE

Requirements
Must have
• A cool look

```html
<!DOCTYPE html>
<html lang="en">
<head>
<meta charset="utf-8">
<title>The Kestrel Personal Training Studio – Information Card</title>
<link href="https://fonts.googleapis.com/css2?family=Montserrat:wght@400;500;600;700;800&display=swap" rel="stylesheet">
<style>
  :root {
    --page: #c2c2c2;
    --card: #333132;
    --red: #ee2e37;
    --white: #ffffff;
    --photo-light: #d9d9d9;
    --photo-mid: #a9a9a9;
  }
  * { box-sizing: border-box; margin: 0; padding: 0; }
  html, body { width: 1200px; height: 1200px; overflow: hidden; background: var(--page); }
  body { position: relative; font-family: "Montserrat", sans-serif; color: var(--white); }

  .card {
    position: absolute; top: 211px; width: 360px; height: 810px;
    background: var(--card); overflow: hidden;
  }
  .card--front { left: 181px; }
  .card--back { left: 661px; }

  .brand {
    position: absolute; left: 26px; top: 34px;
    display: flex; align-items: center; gap: 7px;
    font-weight: 800; font-size: 22px; letter-spacing: 0.5px; color: var(--white);
    z-index: 3;
  }
  .brand__square { width: 12px; height: 12px; background: var(--red); }

  .art { position: absolute; left: 0; top: 0; width: 360px; height: 810px; }

  .headline {
    position: absolute; left: 28px; top: 356px;
    font-size: 28px; line-height: 30px; font-weight: 700; text-transform: uppercase;
  }
  .headline .accent { color: var(--red); font-weight: 500; }

  .rates-tag {
    position: absolute; left: 27px; top: 492px; height: 24px; padding: 0 8px;
    background: var(--red); font-size: 14px; font-weight: 500; line-height: 24px;
  }
  .rates { position: absolute; left: 27px; top: 528px; font-size: 14px; line-height: 20px; }
  .rates ul { list-style: none; }
  .rates li { position: relative; padding-left: 18px; }
  .rates li::before {
    content: ""; position: absolute; left: 0; top: 8px; width: 6px; height: 6px;
    border-radius: 50%; background: var(--red);
  }
  .price { color: var(--red); }
  .example {
    position: absolute; left: 28px; top: 644px; width: 310px;
    font-size: 11px; line-height: 14px; font-weight: 500;
  }
  .example b { font-weight: 700; }

  .contact {
    position: absolute; left: 42px; top: 732px; width: 277px; height: 46px;
    border: 1px solid var(--white); border-top: none; border-bottom: none; text-align: center;
  }
  .contact::before, .contact::after {
    content: ""; position: absolute; height: 1px; background: var(--white);
  }
  .contact::before { top: 0; left: 0; right: 0; }
  .contact::after { bottom: 0; left: 0; right: 0; }
  .contact__phone {
    position: absolute; left: 50%; top: -16px; transform: translateX(-50%);
    background: var(--red); padding: 0 6px;
    font-size: 25px; font-weight: 600; white-space: nowrap;
  }
  .contact__line { font-size: 12px; line-height: 18px; }
  .contact__lines { position: absolute; left: -20px; right: -20px; top: 11px; }
  .contact__lines .contact__line:last-child { background: var(--red); display: inline-block; padding: 0 6px; }

  .section-title {
    position: absolute; left: 28px; font-size: 15px; line-height: 18px;
    font-weight: 800; text-transform: uppercase; letter-spacing: 0.4px; z-index: 2;
  }
  .section-title::after {
    content: ""; display: block; width: 56px; height: 2px; background: var(--red); margin-top: 7px;
  }
  .body-copy {
    position: absolute; left: 28px; font-size: 12px; line-height: 15px; z-index: 2;
  }
</style>
</head>
<body>

<section class="card card--front">
  <svg class="art" viewBox="0 0 360 810" aria-hidden="false">
    <defs>
      <linearGradient id="gymGrey" x1="0" y1="0" x2="1" y2="1">
        <stop offset="0" stop-color="#c9c9c9"/>
        <stop offset="0.5" stop-color="#e2e2e2"/>
        <stop offset="1" stop-color="#b5b5b5"/>
      </linearGradient>
      <clipPath id="photoClip">
        <polygon points="0,130 30,122 55,128 90,112 120,108 150,100 175,82 205,66 240,45 275,42 300,54 330,50 360,58 360,270 335,284 305,300 270,318 235,328 200,338 170,330 135,326 100,318 60,312 25,318 0,316"/>
      </clipPath>
    </defs>
    <g clip-path="url(#photoClip)">
      <rect x="0" y="0" width="360" height="360" fill="url(#gymGrey)" role="img" aria-label="Photo of an athletic man lifting a dumbbell in a bright gym"/>
      <polygon points="0,218 360,147 360,159 0,230" fill="var(--red)"/>
      <polygon points="0,236 360,166 360,178 0,248" fill="var(--red)"/>
      <polygon points="0,256 360,185 360,197 0,268" fill="var(--red)"/>
    </g>
    <polygon points="0,698 30,690 60,700 95,686 130,694 160,684 195,696 230,682 265,692 300,680 330,690 360,684 360,810 0,810" fill="var(--red)"/>
  </svg>

  <div class="brand"><span class="brand__square"></span>THE KESTREL</div>

  <h1 class="headline">A safe and<br><span class="accent">individualized</span><br>approach to<br><span class="accent">strength</span> training.</h1>

  <div class="rates-tag">Our Rates :</div>
  <div class="rates">
    <p>All Sessions are 60 minutes</p>
    <ul>
      <li>1 time per week:&nbsp; <span class="price">$110</span> per session</li>
      <li>2 times per week: <span class="price">$85</span> per session</li>
      <li>3 times per week <span class="price">$80</span> per session</li>
      <li>Add <span class="price">$40</span> for a Partnered Session</li>
    </ul>
  </div>
  <p class="example"><b>Example :</b> A Partnered Session (2 people training together) coming twice a week is $125 per session</p>

  <div class="contact">
    <div class="contact__phone">555.204.7316</div>
    <div class="contact__lines">
      <div class="contact__line">contact@thekestreltraining.com</div>
      <div class="contact__line">www.thekestreltraining.com</div>
    </div>
  </div>
</section>

<section class="card card--back">
  <svg class="art" viewBox="0 0 360 810">
    <defs>
      <linearGradient id="gymDark" x1="0" y1="0" x2="0" y2="1">
        <stop offset="0" stop-color="#333132"/>
        <stop offset="0.35" stop-color="#2b2a28"/>
        <stop offset="1" stop-color="#3a3836"/>
      </linearGradient>
    </defs>
    <rect x="286" y="0" width="12" height="520" fill="var(--red)"/>
    <rect x="303" y="0" width="12" height="520" fill="var(--red)"/>
    <rect x="320" y="0" width="12" height="520" fill="var(--red)"/>
    <rect x="0" y="440" width="360" height="270" fill="url(#gymDark)" role="img" aria-label="Photo of a muscular man curling a dumbbell in a dim gym"/>
    <polygon points="0,698 30,690 60,700 95,686 130,694 160,684 195,696 230,682 265,692 300,680 330,690 360,684 360,810 0,810" fill="var(--red)"/>
  </svg>

  <div class="brand"><span class="brand__square"></span>THE KESTREL</div>

  <h2 class="section-title" style="top:97px;">How do you get started?</h2>
  <p class="body-copy" style="top:140px; width:240px;">We schedule prospective clients for a no cost or obligation consultation. At that consultation we will do a move&shy;ment screen with you. This will allow the trainer to see what level of flexibil&shy;ity and strength you are currently at. You will be able to discuss your goals and other issues (injuries, etc) at that time.</p>

  <h2 class="section-title" style="top:284px;">Our clients<br>have different goals :</h2>
  <p class="body-copy" style="top:346px; width:230px;">Build strength, Increase Flexibility, Improve functional and daily move&shy;ments, Train for an event, or Weight Loss. We will tailor your training program to the specific results you are looking for.</p>
  <p class="body-copy" style="top:446px;">Some ways of training increase the<br>chance of injury, we do not<br>practice those types of training<br>at The Kestrel. Many of our<br>clients have current or past<br>injuries that can cause<br>problems. We work with<br>them to not aggravate<br>&nbsp;those injuries or allow<br>them to become an<br>obstacle to their<br>workouts.</p>

  <div class="contact">
    <div class="contact__phone">555.204.7316</div>
    <div class="contact__lines">
      <div class="contact__line">contact@thekestreltraining.com</div>
      <div class="contact__line">www.thekestreltraining.com</div>
    </div>
  </div>
</section>

</body>
</html>
```